Chamber of Commerce Web Design Project

We are working with Harborlight Chamber of Commerce. They are a new chamber of commerce forming in SoCal.
Some sites to use for inspiration:
https://brevinmarchamber.org
https://quellford.org
https://www.dorwickhavenchamber.com
https://www.tpchamber.com
https://velmorintcc.org
Thank you for taking the time to consider designing a website for us. We are web developers based in Stockton, CA, USA. Most of our projects go through the same process. Understanding this process may help you win a project with us. We custom-code all of our websites in-house. We don’t have any requirements as to what tools you use for your design, but we prefer Figma files. For any design that we label as four-stars, we send it to the client for review. The client picks the final design they want us to use. Once we complete this process, we will continue to show additional clients all the four-star sites and purchase them later. Your designs will have multiple chances to sell. For better chances of success, we ask that you follow these guidelines.
IMAGES:
If you use any images or icons in the design, we ask that you have a link to the asset so we can purchase the image/icon. Most of the designs we submit do not have the customer’s images on them unless they have some great images. Be creative; show us the feeling you are trying to portray with your image choices. Use any royalty-free site you choose. We subscribe to Adobe and mainly use their images, but we can purchase images outside of Adobe.
PLEASE NOTE: we will not submit designs to clients with watermarks on the images.
FONTS:
We ask that you identify the fonts used in the design. This can be done in a message if you want. We typically use Google Fonts and Adobe Fonts.
CONTENT:
We're always open to different content and ideas. We often submit designs with stock images so the client can see our vision. We typically take pictures after the website launch to use their images with our vision. Lorem Ipsum is fine for paragraphs, but we ask that you write the headers in correct English. We want to be able to show the vision and identify the sections of the website.
INSPIRATION:
We typically add a couple of links in the brief of websites we like to help you get started in your design.
REVISIONS:
We do not often ask for revisions of the designs unless we see something in the design that may not appeal to the client. If there are slight changes that we want to make, we do that in the development process.
FEEDBACK:
We rarely give feedback on designs during the design process. We are working on many website projects and do not have the time to provide feedback. We usually respond if your request is well thought out and asks specific questions, but a note asking “feedback, please” usually goes unanswered.

```html
<!DOCTYPE html>
<html lang="en">
<head>
<meta charset="utf-8">
<title>Harborlight Chamber of Commerce</title>
<link rel="stylesheet" href="https://fonts.googleapis.com/css2?family=Oswald:wght@500;600&family=Open+Sans:wght@400;600;700&family=Dancing+Script:wght@700&display=swap">
<style>
:root{
  --blue:#1677ee;
  --yellow:#f8c51f;
  --ink:#222;
  --text:#3a3a3a;
  --light:#f3f3f3;
  --footer:#3d3d3d;
  --white:#fff;
}
*{box-sizing:border-box;margin:0;padding:0}
html,body{width:1200px;height:4317px;overflow:hidden}
body{font-family:"Open Sans",Arial,sans-serif;color:var(--text);background:var(--white);position:relative}
.abs{position:absolute}
.heading{font-family:"Oswald",Impact,sans-serif;font-weight:600;color:var(--ink);text-transform:uppercase;letter-spacing:.3px}
.center{left:0;width:1200px;text-align:center}
.btn{position:absolute;display:flex;align-items:center;justify-content:center;gap:8px;background:var(--blue);color:#fff;font-weight:700;font-size:15px;border-radius:6px;text-transform:uppercase}
.dot{width:14px;height:14px;border-radius:50%;background:#fff;display:inline-flex;align-items:center;justify-content:center}

/* header */
.site-header{top:0;left:0;width:1200px;height:85px;background:#fff}
.brand{left:143px;top:14px;display:flex;align-items:center;gap:10px}
.brand-mark{width:54px;height:54px;border-radius:50%;background:var(--yellow);flex:none}
.brand-name{font-family:"Oswald",sans-serif;font-weight:600;color:var(--blue);font-size:19px;line-height:23px;text-transform:uppercase;width:190px}
.topbar{top:10px;right:146px;display:flex;gap:26px;font-size:11px;color:#555;align-items:center}
.topbar span{display:flex;align-items:center;gap:5px}
.main-nav{top:51px;right:146px;display:flex;gap:30px;font-size:15px;color:#222}
.main-nav .active{color:var(--yellow)}

/* hero */
.hero{top:85px;left:0;width:1200px;height:615px;overflow:hidden}
.hero-photo{position:absolute;inset:0;background:
  radial-gradient(ellipse 230px 330px at 1110px 330px,rgba(62,86,48,.95) 0%,rgba(62,86,48,.6) 45%,rgba(62,86,48,0) 75%),
  radial-gradient(ellipse 180px 160px at 190px 520px,rgba(58,82,44,.85) 0%,rgba(58,82,44,0) 80%),
  radial-gradient(ellipse 520px 70px at 560px 260px,rgba(214,220,226,.9) 0%,rgba(214,220,226,0) 80%),
  linear-gradient(180deg,#8db6dc 0%,#bcd3e6 28%,#8f9bab 36%,#b5c1cc 41%,#d4d9dd 47%,#9aa8b4 52%,#2f6aa0 56%,#2a649a 70%,#5a6e7a 80%,#c9ccca 86%,#3f5a46 100%)}
.hero-title{top:85px;font-size:46px}
.hero-sub{top:160px;left:240px;width:720px;text-align:center;font-size:18px;line-height:33px;color:#111}

/* services */
.section-title{font-size:40px}
.lead{font-size:17px;line-height:32px;color:#555;text-align:center}
.svc-num{font-family:"Oswald",sans-serif;font-weight:600;font-size:46px;color:#3a3a3a;width:120px;text-align:center;line-height:60px}
.svc-icon{width:82px;height:82px;border-radius:50%;background:var(--yellow);display:flex;align-items:center;justify-content:center;border:3px solid #fff;box-shadow:0 2px 6px rgba(0,0,0,.15)}
.svc-label{font-size:16px;color:#222;width:260px;text-align:center}
.svc-photo{left:429px;top:922px;width:344px;height:263px;border-radius:6px;background:
  radial-gradient(ellipse 70px 60px at 172px 95px,rgba(214,170,140,.9) 0%,rgba(214,170,140,0) 100%),
  radial-gradient(ellipse 40px 40px at 75px 120px,rgba(205,150,120,.8) 0%,rgba(205,150,120,0) 100%),
  radial-gradient(ellipse 40px 40px at 265px 125px,rgba(190,140,110,.8) 0%,rgba(190,140,110,0) 100%),
  radial-gradient(ellipse 120px 110px at 172px 230px,rgba(31,52,92,1) 0%,rgba(31,52,92,0) 100%),
  radial-gradient(ellipse 60px 80px at 60px 230px,rgba(140,50,50,.7) 0%,rgba(140,50,50,0) 100%),
  linear-gradient(180deg,#e8e6e1 0%,#d9d4cb 40%,#707a8c 75%,#2b3858 100%)}

/* accelerator */
.accelerator{top:1352px;left:0;width:1200px;height:611px;background:var(--light)}
.acc-card{top:244px;width:296px;height:251px}
.acc-photo{position:absolute;inset:0;border-radius:40px 0 0 0}
.acc-label{position:absolute;left:0;width:100%;text-align:center;color:#fff;font-size:17px}
.acc-icon{position:absolute;left:114px;top:216px;width:68px;height:68px;border-radius:50%;background:var(--yellow);border:5px solid #fff;box-shadow:0 2px 6px rgba(0,0,0,.2);display:flex;align-items:center;justify-content:center}

/* why join */
.why{top:1963px;left:0;width:1200px;height:521px;background:var(--blue);overflow:hidden}
.why-photo{position:absolute;left:560px;top:0;width:640px;height:521px;background:
  radial-gradient(ellipse 150px 180px at 160px 200px,rgba(120,170,235,.55) 0%,rgba(120,170,235,0) 100%),
  radial-gradient(ellipse 170px 220px at 420px 300px,rgba(90,150,230,.6) 0%,rgba(90,150,230,0) 100%),
  radial-gradient(ellipse 120px 160px at 560px 120px,rgba(130,180,240,.45) 0%,rgba(130,180,240,0) 100%),
  linear-gradient(90deg,rgba(22,119,238,0) 0%,rgba(40,130,240,.5) 50%,rgba(22,119,238,.3) 100%)}
.why h2{position:absolute;left:144px;top:58px;color:#fff;font-size:37px}
.why-sub{left:144px;top:124px;width:420px;color:#fff;font-size:18px;line-height:28px}
.why-text{left:144px;width:470px;color:#fff;font-size:13px;line-height:24px}
.btn-outline{position:absolute;left:144px;top:407px;width:153px;height:43px;border:2px solid #fff;border-radius:5px;color:#fff;font-weight:700;font-size:15px;display:flex;align-items:center;justify-content:center;gap:8px}

/* programs */
.prog-photo{height:189px;width:275px}
.prog-card{width:288px;text-align:center}
.prog-date{font-size:13px;color:#555;display:flex;align-items:center;justify-content:center;gap:6px}
.prog-title{font-size:17px;line-height:25px;color:#222;margin-top:8px}
.prog-text{font-size:13px;line-height:20px;color:#666;margin-top:10px}
.prog-more{font-size:14px;font-weight:700;color:var(--blue);margin-top:12px}
.round-arrow{width:38px;height:38px;border-radius:50%;display:flex;align-items:center;justify-content:center}

/* investors */
.partner{top:3325px;height:70px;background:#fff;box-shadow:0 3px 10px rgba(0,0,0,.08);display:flex;align-items:center;justify-content:center;gap:10px;font-size:21px;font-weight:600;color:#333}
.partner i{display:block;width:28px;height:28px;border-radius:50%;background:#333}

/* cta + footer */
.cta{top:3493px;left:0;width:1200px;height:824px;background:
  linear-gradient(100deg,rgba(255,255,255,0) 0%,rgba(255,255,255,.08) 30%,rgba(255,255,255,0) 45%,rgba(255,255,255,.07) 70%,rgba(255,255,255,0) 85%),
  linear-gradient(160deg,#1a7af0 0%,#1672e6 50%,#1f7ff2 100%)}
.cta-item{width:300px;text-align:center;color:#fff}
.cta-icon{width:42px;height:42px;border-radius:50%;background:var(--yellow);margin:0 auto;display:flex;align-items:center;justify-content:center}
.cta-label{font-size:16px;margin-top:10px}
.cta-value{font-size:20px;font-weight:700;color:var(--yellow);margin-top:10px}
.or{font-family:"Dancing Script",cursive;font-size:36px;color:#fff}
.footer-col h4{font-size:16px;font-weight:600;color:#fff;text-transform:uppercase;margin-bottom:12px}
.footer-col li{list-style:none;font-size:13px;color:#fff;line-height:25px}
.social{width:28px;height:28px;border-radius:50%;background:#fff}
</style>
</head>
<body>

<header class="abs site-header">
  <div class="abs brand">
    <span class="brand-mark"></span>
    <span class="brand-name">Harborlight<br>Chamber of Commerce</span>
  </div>
  <div class="abs topbar">
    <span><svg width="10" height="10" viewBox="0 0 24 24"><path d="M6.6 10.8a15 15 0 006.6 6.6l2.2-2.2a1 1 0 011-.25 11.4 11.4 0 003.6.57 1 1 0 011 1V20a1 1 0 01-1 1A17 17 0 013 4a1 1 0 011-1h3.5a1 1 0 011 1c0 1.25.2 2.45.57 3.57a1 1 0 01-.25 1z" fill="#1677ee"/></svg>+1-555-014-2290</span>
    <span style="color:#ccc">|</span>
    <span><svg width="11" height="9" viewBox="0 0 22 16"><rect width="22" height="16" rx="2" fill="#1677ee"/><path d="M1 1l10 8 10-8" stroke="#fff" stroke-width="2" fill="none"/></svg>info@harborlightchamber.org</span>
  </div>
  <nav class="abs main-nav">
    <span class="active">Home</span><span>About</span><span>Services</span><span>Programs</span><span>Resources</span><span>Membership</span><span>Contact</span>
  </nav>
</header>

<section class="hero abs">
  <div class="hero-photo" role="img" aria-label="Photo of a coastal city skyline with mountains, a marina and palm trees"></div>
  <svg class="abs" style="left:0;top:0" width="1200" height="615" viewBox="0 0 1200 615">
    <polygon points="0,468 801,598 1200,448 1200,615 0,615" fill="#f8c51f"/>
    <polygon points="0,505 801,612 1200,492 1200,615 0,615" fill="#fff"/>
  </svg>
  <h1 class="abs heading center hero-title">Welcome to Harborlight Chamber of Commerce</h1>
  <p class="abs hero-sub">Lorem ipsum dolor sit amet, consectetur adipiscing elit, sed do eiusmod tempor incididunt dolore. magna aliqua.</p>
  <div class="btn" style="left:521px;top:255px;width:158px;height:44px;border:2px solid #fff">Get Started <span class="dot"><svg width="8" height="8" viewBox="0 0 10 10"><path d="M3 1l4 4-4 4" stroke="#1677ee" stroke-width="2" fill="none"/></svg></span></div>
</section>

<section class="services">
  <h2 class="abs heading center section-title" style="top:734px">Our Services</h2>
  <p class="abs lead" style="left:200px;top:802px;width:800px">Lorem ipsum dolor sit amet, consectetur adipiscing elit, sed do eiusmod tempor incididunt ut labore et dolore magna aliqua. Ut enim ad minim veniam,</p>

  <svg class="abs" style="left:0;top:900px" width="1200" height="260" viewBox="0 0 1200 260">
    <defs><marker id="arrowhead" markerWidth="8" markerHeight="8" refX="4" refY="4" orient="auto"><path d="M0,0 L8,4 L0,8" fill="none" stroke="#c9c9c9" stroke-width="1.5"/></marker></defs>
    <g stroke="#cfcfcf" stroke-width="2" stroke-dasharray="6 4" fill="none" marker-end="url(#arrowhead)">
      <line x1="422" y1="108" x2="336" y2="75"/>
      <line x1="420" y1="190" x2="332" y2="214"/>
      <line x1="780" y1="108" x2="870" y2="75"/>
      <line x1="780" y1="190" x2="874" y2="214"/>
    </g>
  </svg>

  <div class="abs svc-num" style="left:193px;top:864px">01</div>
  <div class="abs svc-icon" style="left:211px;top:906px"><svg width="42" height="42" viewBox="0 0 40 40" fill="none" stroke="#333" stroke-width="2"><rect x="6" y="12" width="28" height="20" rx="2"/><path d="M15 12V8h10v4M6 20h28"/></svg></div>
  <div class="abs svc-label" style="left:123px;top:1009px">Business Connections</div>

  <div class="abs svc-num" style="left:193px;top:1048px">02</div>
  <div class="abs svc-icon" style="left:211px;top:1090px"><svg width="42" height="42" viewBox="0 0 40 40" fill="none" stroke="#333" stroke-width="2"><rect x="8" y="7" width="24" height="16" rx="3"/><path d="M14 23l-3 5 8-5M13 13h14M13 17h9"/></svg></div>
  <div class="abs svc-label" style="left:123px;top:1193px">Marketing Consultation</div>

  <div class="abs svc-num" style="left:912px;top:864px">03</div>
  <div class="abs svc-icon" style="left:930px;top:906px"><svg width="42" height="42" viewBox="0 0 40 40" fill="none" stroke="#333" stroke-width="2"><circle cx="20" cy="13" r="5"/><circle cx="10" cy="17" r="4"/><circle cx="30" cy="17" r="4"/><path d="M11 32c0-6 4-10 9-10s9 4 9 10M3 30c0-4 3-7 7-7M37 30c0-4-3-7-7-7"/></svg></div>
  <div class="abs svc-label" style="left:842px;top:1009px">Government Relations</div>

  <div class="abs svc-num" style="left:912px;top:1048px">04</div>
  <div class="abs svc-icon" style="left:930px;top:1090px"><svg width="42" height="42" viewBox="0 0 40 40" fill="none" stroke="#333" stroke-width="2"><rect x="5" y="8" width="26" height="22"/><path d="M10 25v-5M16 25v-9M22 25v-6"/><circle cx="28" cy="26" r="5"/><path d="M32 30l4 4"/></svg></div>
  <div class="abs svc-label" style="left:842px;top:1193px">Market Research</div>

  <div class="abs svc-photo" role="img" aria-label="Photo of a smiling business team standing together"></div>
  <div class="btn" style="left:525px;top:1232px;width:150px;height:43px">Learn More <span class="dot"><svg width="8" height="8" viewBox="0 0 10 10"><path d="M3 1l4 4-4 4" stroke="#1677ee" stroke-width="2" fill="none"/></svg></span></div>
</section>

<section class="abs accelerator">
  <h2 class="abs heading center section-title" style="top:76px">Your Business Accelerator</h2>
  <p class="abs lead" style="left:210px;top:140px;width:780px;font-size:16px;line-height:28px">Sed ut perspiciatis unde omnis iste natus error sit voluptatem accusantium doloremque laudantium, totam rem aperiam, eaque ipsa quae ab illo inventore veritatis .</p>

  <div class="abs acc-card" style="left:144px">
    <div class="acc-photo" role="img" aria-label="Photo of colleagues reviewing charts at a desk" style="background:
      radial-gradient(ellipse 60px 70px at 230px 70px,rgba(200,160,130,.8) 0%,rgba(200,160,130,0) 100%),
      radial-gradient(ellipse 80px 50px at 110px 140px,rgba(225,230,238,.9) 0%,rgba(225,230,238,0) 100%),
      radial-gradient(ellipse 90px 120px at 250px 180px,rgba(40,38,40,.9) 0%,rgba(40,38,40,0) 100%),
      linear-gradient(160deg,#c6c0b8 0%,#8e8882 45%,#3b3838 100%)"></div>
    <div class="acc-label" style="top:182px">Convene</div>
    <div class="acc-icon"><svg width="30" height="30" viewBox="0 0 30 30" fill="none" stroke="#333" stroke-width="1.8"><path d="M5 8h14v9H10l-4 3v-3H5z"/><path d="M19 12h6v8h-2v3l-3-3h-6v-3"/></svg></div>
  </div>
  <div class="abs acc-card" style="left:452px">
    <div class="acc-photo" role="img" aria-label="Photo of a woman working on a laptop on a sofa" style="background:
      radial-gradient(ellipse 50px 60px at 150px 75px,rgba(205,160,130,.85) 0%,rgba(205,160,130,0) 100%),
      radial-gradient(ellipse 80px 50px at 280px 40px,rgba(150,80,55,.7) 0%,rgba(150,80,55,0) 100%),
      radial-gradient(ellipse 130px 70px at 150px 220px,rgba(60,60,62,.9) 0%,rgba(60,60,62,0) 100%),
      linear-gradient(160deg,#d6d1cb 0%,#9a948e 45%,#4a4846 100%)"></div>
    <div class="acc-label" style="top:168px">Navigate</div>
    <div class="acc-icon"><svg width="30" height="30" viewBox="0 0 30 30" fill="none" stroke="#333" stroke-width="1.8"><rect x="6" y="5" width="18" height="20" rx="2"/><path d="M15 10l4 5-4 5-4-5z"/></svg></div>
  </div>
  <div class="abs acc-card" style="left:759px">
    <div class="acc-photo" role="img" aria-label="Photo of a diverse group of professionals in an office" style="background:
      radial-gradient(ellipse 45px 55px at 80px 70px,rgba(140,95,70,.85) 0%,rgba(140,95,70,0) 100%),
      radial-gradient(ellipse 45px 55px at 170px 85px,rgba(215,180,150,.85) 0%,rgba(215,180,150,0) 100%),
      radial-gradient(ellipse 45px 55px at 245px 80px,rgba(100,70,55,.85) 0%,rgba(100,70,55,0) 100%),
      radial-gradient(ellipse 160px 90px at 150px 220px,rgba(30,30,36,.95) 0%,rgba(30,30,36,0) 100%),
      linear-gradient(160deg,#e6e4e0 0%,#a4a5a8 45%,#3a3b40 100%)"></div>
    <div class="acc-label" style="top:170px">Advocate</div>
    <div class="acc-icon"><svg width="30" height="30" viewBox="0 0 30 30" fill="none" stroke="#333" stroke-width="1.8"><circle cx="11" cy="11" r="3"/><circle cx="19" cy="11" r="3"/><path d="M5 23c0-4 3-7 6-7s6 3 6 7M13 23c0-4 3-7 6-7s6 3 6 7"/></svg></div>
  </div>
</section>

<section class="abs why">
  <div class="why-photo" role="img" aria-label="Blue-tinted photo of business people collaborating"></div>
  <h2 class="heading">Why Join the Chamber?</h2>
  <p class="abs why-sub">Nemo enim ipsam voluptatem quia voluptas sit aspernatur aut odit aut fugit, sed quia</p>
  <p class="abs why-text" style="top:200px">Lorem ipsum dolor sit amet, consectetur adipiscing elit, sed do eiusmod tempor incididunt ut labore et dolore magna aliqua. Ut enim ad minim veniam, quis nostrud exercitation ullamco laboris nisi.</p>
  <p class="abs why-text" style="top:283px">Sed ut perspiciatis unde omnis iste natus error sit voluptatem accusantium doloremque laudantium, totam rem aperiam, eaque ipsa quae ab illo inventore veritatis et quasi architecto beatae vitae dicta sunt explicabo. ut aliquip ex ea commodo consequat.</p>
  <div class="btn-outline">LEARN MORE <span class="dot"><svg width="8" height="8" viewBox="0 0 10 10"><path d="M3 1l4 4-4 4" stroke="#1677ee" stroke-width="2" fill="none"/></svg></span></div>
</section>

<section class="programs">
  <h2 class="abs heading center section-title" style="top:2570px">Programs &amp; Events</h2>
  <div class="abs" style="left:456px;top:2640px;width:288px;height:402px;background:#fff;box-shadow:0 4px 14px rgba(0,0,0,.12)"></div>

  <div class="abs round-arrow" style="left:71px;top:2808px;background:#9a9a9a"><svg width="12" height="12" viewBox="0 0 10 10"><path d="M7 1L3 5l4 4" stroke="#fff" stroke-width="2" fill="none"/></svg></div>
  <div class="abs round-arrow" style="left:1091px;top:2808px;background:#333"><svg width="12" height="12" viewBox="0 0 10 10"><path d="M3 1l4 4-4 4" stroke="#fff" stroke-width="2" fill="none"/></svg></div>

  <div class="abs prog-card" style="left:144px;top:2653px">
    <div class="prog-photo" style="margin-left:7px;background:
      radial-gradient(ellipse 50px 80px at 70px 70px,rgba(180,85,45,.95) 0%,rgba(180,85,45,0) 100%),
      radial-gradient(ellipse 60px 45px at 170px 85px,rgba(240,240,240,.95) 0%,rgba(240,240,240,0) 100%),
      radial-gradient(ellipse 70px 40px at 230px 150px,rgba(200,90,80,.7) 0%,rgba(200,90,80,0) 100%),
      radial-gradient(ellipse 140px 40px at 140px 175px,rgba(235,235,232,.9) 0%,rgba(235,235,232,0) 100%),
      linear-gradient(180deg,#e3e6e8 0%,#b9c2c8 50%,#8c96a0 100%)" role="img" aria-label="Photo of a team meeting around a screen with charts"></div>
    <div style="margin-top:26px" class="prog-date"><svg width="12" height="12" viewBox="0 0 12 12"><rect x="1" y="2" width="10" height="9" fill="none" stroke="#555" stroke-width="1.3"/><path d="M1 5h10M4 1v2M8 1v2" stroke="#555" stroke-width="1.3"/></svg>February 2, 2021</div>
    <div class="prog-title">Lorem ipsum dolor sit amet,<br>consectetur adipiscing</div>
    <div class="prog-text">Sed ut perspiciatis unde omnis iste natus<br>sit voluptatem accusantium</div>
    <div class="prog-more">READ MORE &rsaquo;</div>
  </div>
  <div class="abs prog-card" style="left:456px;top:2653px">
    <div class="prog-photo" style="margin-left:7px;background:
      radial-gradient(ellipse 40px 60px at 50px 90px,rgba(60,60,64,.9) 0%,rgba(60,60,64,0) 100%),
      radial-gradient(ellipse 45px 60px at 150px 80px,rgba(110,110,115,.8) 0%,rgba(110,110,115,0) 100%),
      radial-gradient(ellipse 45px 65px at 235px 90px,rgba(70,55,50,.85) 0%,rgba(70,55,50,0) 100%),
      radial-gradient(ellipse 150px 35px at 140px 170px,rgba(250,250,250,.95) 0%,rgba(250,250,250,0) 100%),
      linear-gradient(180deg,#d9d9d7 0%,#c3c2bf 50%,#e9e9e7 100%)" role="img" aria-label="Photo of colleagues talking at a meeting table"></div>
    <div style="margin-top:26px" class="prog-date"><svg width="12" height="12" viewBox="0 0 12 12"><rect x="1" y="2" width="10" height="9" fill="none" stroke="#555" stroke-width="1.3"/><path d="M1 5h10M4 1v2M8 1v2" stroke="#555" stroke-width="1.3"/></svg>February 2, 2021</div>
    <div class="prog-title">Lorem ipsum dolor sit amet,<br>consectetur adipiscing</div>
    <div class="prog-text">Sed ut perspiciatis unde omnis iste natus<br>sit voluptatem accusantium</div>
    <div class="prog-more">READ MORE &rsaquo;</div>
  </div>
  <div class="abs prog-card" style="left:772px;top:2653px">
    <div class="prog-photo" style="margin-left:7px;background:
      radial-gradient(ellipse 40px 80px at 70px 110px,rgba(200,175,130,.85) 0%,rgba(200,175,130,0) 100%),
      radial-gradient(ellipse 40px 80px at 120px 110px,rgba(170,45,40,.9) 0%,rgba(170,45,40,0) 100%),
      radial-gradient(ellipse 90px 90px at 215px 90px,rgba(40,55,80,.95) 0%,rgba(40,55,80,0) 100%),
      linear-gradient(160deg,#d2d6da 0%,#9aa3ad 40%,#384660 100%)" role="img" aria-label="Photo of two professionals discussing data on a large display"></div>
    <div style="margin-top:26px" class="prog-date"><svg width="12" height="12" viewBox="0 0 12 12"><rect x="1" y="2" width="10" height="9" fill="none" stroke="#555" stroke-width="1.3"/><path d="M1 5h10M4 1v2M8 1v2" stroke="#555" stroke-width="1.3"/></svg>February 2, 2021</div>
    <div class="prog-title">Lorem ipsum dolor sit amet,<br>consectetur adipiscing</div>
    <div class="prog-text">Sed ut perspiciatis unde omnis iste natus<br>sit voluptatem accusantium</div>
    <div class="prog-more">READ MORE &rsaquo;</div>
  </div>
</section>

<section class="investors">
  <h2 class="abs heading center section-title" style="top:3138px">Investors in the Regions’ Success</h2>
  <p class="abs center" style="top:3206px;font-size:17px;color:#222">Lorem ipsum dolor sit amet, consectetur adipiscing elit, sed do eiusmod tempor</p>
  <p class="abs" style="left:150px;top:3245px;width:900px;text-align:center;font-size:13px;line-height:24px;color:#666">Duis aute irure dolor in reprehenderit in voluptate velit esse cillum dolore eu fugiat nulla pariatur,excepteur sint occaecat cupidatat non proident, sunt in culpa qui officia deserunt mollit anim id est laborum.</p>

  <div class="abs round-arrow" style="left:78px;top:3345px;background:#fff;box-shadow:0 2px 6px rgba(0,0,0,.15);width:32px;height:32px"><svg width="10" height="10" viewBox="0 0 10 10"><path d="M7 1L3 5l4 4z" fill="#333"/></svg></div>
  <div class="abs round-arrow" style="left:1088px;top:3345px;background:#fff;box-shadow:0 2px 6px rgba(0,0,0,.15);width:32px;height:32px"><svg width="10" height="10" viewBox="0 0 10 10"><path d="M3 1l4 4-4 4z" fill="#333"/></svg></div>

  <div class="abs partner" style="left:142px;width:215px"><i></i>Northvale</div>
  <div class="abs partner" style="left:373px;width:217px"><i></i>Kestrel</div>
  <div class="abs partner" style="left:605px;width:216px"><i></i>Brightwater</div>
  <div class="abs partner" style="left:836px;width:218px"><i></i>Ondera</div>
</section>

<section class="abs cta" role="img" aria-label="Blue-tinted photo of city office towers"></section>
<h2 class="abs heading center" style="top:3558px;color:#fff;font-size:38px">Ready to Get Started?</h2>
<p class="abs center" style="top:3632px;font-size:18px;color:#fff">Duis aute irure dolor in reprehenderit in voluptate velit esse cillum dolore</p>

<div class="abs cta-item" style="left:286px;top:3686px">
  <div class="cta-icon"><svg width="18" height="14" viewBox="0 0 22 16"><rect width="22" height="16" rx="2" fill="#333"/><path d="M1 1l10 8 10-8" stroke="#f8c51f" stroke-width="2" fill="none"/></svg></div>
  <div class="cta-label">Email Us</div>
  <div class="cta-value">info@hlcoc.org</div>
</div>
<svg class="abs" style="left:538px;top:3720px" width="116" height="30" viewBox="0 0 116 30"><path d="M4 24 Q58 0 110 12" stroke="#fff" stroke-width="2" fill="none"/><path d="M102 6l9 6-10 4" stroke="#fff" stroke-width="2" fill="none"/></svg>
<div class="abs or" style="left:578px;top:3738px">or</div>
<div class="abs cta-item" style="left:616px;top:3686px">
  <div class="cta-icon"><svg width="18" height="18" viewBox="0 0 24 24"><path d="M6.6 10.8a15 15 0 006.6 6.6l2.2-2.2a1 1 0 011-.25 11.4 11.4 0 003.6.57 1 1 0 011 1V20a1 1 0 01-1 1A17 17 0 013 4a1 1 0 011-1h3.5a1 1 0 011 1c0 1.25.2 2.45.57 3.57a1 1 0 01-.25 1z" fill="#333"/></svg></div>
  <div class="cta-label">Call Us</div>
  <div class="cta-value">+1-555-014-2290</div>
</div>

<footer>
  <svg class="abs" style="left:0;top:3860px" width="1200" height="457" viewBox="0 0 1200 457">
    <polygon points="0,165 637,0 1200,120 1200,457 0,457" fill="#f8c51f"/>
    <polygon points="0,180 637,22 1200,142 1200,457 0,457" fill="#3d3d3d"/>
  </svg>

  <div class="abs" style="left:143px;top:4040px;display:flex;align-items:center;gap:8px">
    <span style="width:44px;height:44px;border-radius:50%;background:var(--yellow);display:block"></span>
    <span style="font-family:'Oswald',sans-serif;font-weight:600;color:var(--blue);font-size:16px;line-height:19px;text-transform:uppercase;width:170px">Harborlight<br>Chamber of Commerce</span>
  </div>
  <p class="abs" style="left:143px;top:4104px;width:210px;font-size:11.5px;line-height:21px;color:#fff">Nemo enim ipsam voluptatem quia voluptas sit aspernatur aut odit aut fugit, sed quia consequuntur</p>

  <div class="abs footer-col" style="left:431px;top:4020px">
    <h4>Information</h4>
    <ul><li>Home</li><li>About</li><li>Services</li><li>Programs</li><li>Resources</li><li>Membership</li><li>Events</li><li>Contact</li></ul>
  </div>
  <div class="abs footer-col" style="left:620px;top:4020px">
    <h4>Other Links</h4>
    <ul><li>Login</li><li>Join</li><li>News</li><li>Privacy</li></ul>
  </div>
  <div class="abs footer-col" style="left:813px;top:4020px;width:245px">
    <h4 style="font-weight:700">Stay in the Know</h4>
    <p style="font-size:12.5px;line-height:19px;color:#fff;margin-top:-4px">Lorem ipsum dolor sit amet, consectetur adipiscing elit, sed do eiusmod</p>
  </div>
  <div class="abs" style="left:813px;top:4108px;width:234px;height:33px;background:#fff;border-radius:17px;display:flex;align-items:center;justify-content:space-between;padding:0 14px;font-size:10px;color:#999">
    <span>Email Address</span>
    <svg width="16" height="14" viewBox="0 0 16 14"><path d="M0 6L16 0 12 14 8 9z" fill="#1677ee"/></svg>
  </div>
  <div class="abs" style="left:813px;top:4160px;display:flex;gap:9px">
    <span class="social"></span><span class="social" style="background:var(--yellow)"></span><span class="social"></span>
  </div>

  <div class="abs" style="left:143px;top:4264px;width:911px;height:1px;background:#5a5a5a"></div>
  <p class="abs center" style="top:4282px;font-size:12px;color:#fff">Copyright© 2025 Harborlight Chamber of Commerce &nbsp;|&nbsp; All Rights Reserved</p>
</footer>

</body>
</html>
```